Fresh, modern, fun business card for pediatric dental practice

Need a business card for fresh, modern, fun pediatric dental practice

Clean look that matches our website's font and colors

We prefer the look of curved corners on business cards

Target Market(s)

parents (mothers) of young children, professionals, mid-high class

Industry/Entity Type

Dental

Contact Information for Business Card

Maplebrook Pediatric Dentistry
482 Quarry Lane
Suite 517
Fernhollow, PA 17990
717.555.0193
www.maplebrookkidsdental.example

Mei-Ran Tsai, DMD
Corinne Walbeck, DMD
(we are working on our email address, but we would like that on the card as well)

Font styles to use
Sans Serif

Requirements
Must have
• All info; we would also like to make cards for individual staff members
• colors from our website and color palatte, attatched
• use same font and design as website for branding
Nice to have
• clean, simple card that has a pop of color
• we would like to see a few designs with our tag line "where smiles get brighter"
• we are not sure if we want to have it on there or not
• we would like to see a few designs incorporating the ribbon graphic on our website where the word WELCOME is

```html
<!DOCTYPE html>
<html lang="en">
<head>
<meta charset="utf-8">
<title>Maplebrook Pediatric Dentistry – Business Card</title>
<link rel="stylesheet" href="https://fonts.googleapis.com/css2?family=Roboto:wght@400;500&family=Roboto+Condensed:wght@500&display=swap">
<style>
  :root {
    --backdrop: #2b2b2b;
    --card-white: #f3f3f3;
    --sun-yellow: #efb324;
    --berry: #c72d8a;
    --ink-grey: #4a4a4a;
    --divider: #c9c9c9;
    --paper-white: #ffffff;
  }
  * { margin: 0; padding: 0; box-sizing: border-box; }
  html, body {
    width: 1200px; height: 960px; overflow: hidden;
    background: var(--backdrop);
    font-family: "Roboto", Arial, sans-serif;
  }
  .stage { position: relative; width: 1200px; height: 960px; }

  .card {
    position: absolute;
    width: 600px; height: 342px;
    border-radius: 22px;
    overflow: hidden;
  }
  .card--front { left: 314px; top: 113px; background: var(--card-white); }
  .card--back { left: 311px; top: 472px; background: var(--sun-yellow); }

  /* front: brand block */
  .brand {
    position: absolute; left: 50px; top: 96px; width: 244px;
    text-align: center; color: var(--sun-yellow); font-weight: 500;
  }
  .brand__dot {
    display: block; width: 34px; height: 34px; border-radius: 50%;
    background: var(--sun-yellow); margin: 0 auto 14px;
  }
  .brand__name { font-size: 38px; line-height: 40px; letter-spacing: 0.5px; }
  .brand__sub { font-size: 19px; line-height: 24px; letter-spacing: 0.6px; }

  .divider {
    position: absolute; left: 311px; top: 72px;
    width: 1px; height: 176px; background: var(--divider);
  }

  /* front: contact block */
  .contact { position: absolute; left: 337px; top: 80px; }
  .contact__doctors {
    font-family: "Roboto Condensed", "Arial Narrow", sans-serif;
    font-weight: 500; font-size: 21px; line-height: 24px;
    color: var(--sun-yellow); margin-bottom: 6px;
  }
  .contact__address {
    font-size: 14.5px; line-height: 18px; color: var(--ink-grey);
    font-style: normal;
  }
  .contact__phone {
    display: flex; align-items: center; gap: 6px;
    margin-top: 12px; font-size: 14.5px; color: var(--ink-grey);
  }
  .contact__phone svg { width: 13px; height: 13px; fill: var(--sun-yellow); }

  .wave { position: absolute; left: 0; top: 0; width: 600px; height: 342px; }
  .web {
    position: absolute; left: 0; right: 0;
    text-align: center; color: var(--paper-white);
    font-size: 13.5px; letter-spacing: 3.2px; white-space: nowrap;
  }
  .card--front .web { top: 313px; }

  /* back */
  .emblem {
    position: absolute; left: 0; right: 0; top: 88px;
    text-align: center; color: var(--paper-white); font-weight: 500;
  }
  .emblem__dot {
    display: block; width: 96px; height: 96px; border-radius: 50%;
    background: var(--paper-white); margin: 0 auto 22px;
  }
  .emblem__name { font-size: 26px; line-height: 32px; letter-spacing: 0.6px; }
  .card--back .web { top: 294px; }
</style>
</head>
<body>
<main class="stage">
  <section class="card card--front" aria-label="Business card front">
    <div class="brand">
      <span class="brand__dot"></span>
      <div class="brand__name">Maplebrook</div>
      <div class="brand__sub">pediatric dentistry</div>
    </div>
    <div class="divider"></div>
    <div class="contact">
      <p class="contact__doctors">Mei-Ran Tsai, DMD<br>Corinne Walbeck, DMD</p>
      <address class="contact__address">
        Maplebrook Pediatric Dentistry<br>
        482 Quarry Lane<br>
        Suite 517<br>
        Fernhollow, PA 17990
      </address>
      <p class="contact__phone">
        <svg viewBox="0 0 24 24" aria-hidden="true"><path d="M6.6 10.8a15.1 15.1 0 0 0 6.6 6.6l2.2-2.2a1 1 0 0 1 1-.25 11.4 11.4 0 0 0 3.6.57 1 1 0 0 1 1 1V20a1 1 0 0 1-1 1A17 17 0 0 1 3 4a1 1 0 0 1 1-1h3.5a1 1 0 0 1 1 1c0 1.250.2 2.45.57 3.6a1 1 0 0 1-.25 1z"/></svg>
        717.555.0193
      </p>
    </div>
    <svg class="wave" viewBox="0 0 600 342" aria-hidden="true">
      <path d="M0 320 Q300 276 600 320" fill="none" stroke="var(--sun-yellow)" stroke-width="4"/>
      <path d="M0 327 Q300 285 600 327 L600 342 L0 342 Z" fill="var(--berry)"/>
    </svg>
    <p class="web">www.maplebrookkidsdental.example</p>
  </section>

  <section class="card card--back" aria-label="Business card back">
    <div class="emblem">
      <span class="emblem__dot"></span>
      <div class="emblem__name">Maplebrook Pediatric Dentistry</div>
    </div>
    <p class="web">www.maplebrookkidsdental.example</p>
  </section>
</main>
</body>
</html>
```